Tabloid Magazine Flyer Class Action Lawsuit

Create a bold, 2-page 8.5" x 11" flyer with the look and feel of a tabloid exposé — loud, sensational, and impossible to ignore. Use bold fonts, dramatic headlines, and high-contrast colors (red, black, white, deep blue). Fill every inch of space — no white space, no subtlety. Use the provided images prominently. Page 1 should grab attention with a shocking headline, impactful image, and strong call to action. Page 2 should stack bold subheadings and explosive bullet points. Emphasize urgency, outrage, and grassroots power. This flyer is meant to rally a community.
Updates

Need to extend because we haven't received a design that meets our needs

Target Market(s)

All instructions and content are in the attached word doc

Industry/Entity Type

Requirements
Must have
• All instructions and content are in the attached word doc
Nice to have
Should not have

```html
<!DOCTYPE html>
<html lang="en">
<head>
<meta charset="utf-8">
<title>Seacliff Park Flyer</title>
<link rel="stylesheet" href="https://fonts.googleapis.com/css2?family=Anton&family=Poppins:wght@600;700&family=Arimo:wght@500;700&display=swap">
<style>
  :root {
    --backdrop: #8c8b8c;
    --paper: #ffffff;
    --red: #d30f12;
    --blue: #1466c6;
    --navy: #1b2a3a;
    --ink: #111111;
    --dark-red: #2a0a0a;
  }
  * { box-sizing: border-box; margin: 0; padding: 0; }
  html, body { width: 1200px; height: 2369px; overflow: hidden; background: var(--backdrop); }
  .canvas { position: relative; width: 1200px; height: 2369px; }
  .page { position: absolute; left: 189px; width: 823px; height: 1058px; background: var(--paper); overflow: hidden; }
  .page-one { top: 112px; }
  .page-two { top: 1236px; }
  .abs { position: absolute; }
  .headline-art { position: absolute; left: 0; top: 0; width: 823px; height: 1058px; pointer-events: none; }
  .display { font-family: "Anton", sans-serif; }

  .teaser {
    left: 490px; top: 35px; width: 293px; height: 227px; background: var(--navy);
    color: #fff; font-family: "Poppins", sans-serif; font-weight: 700; font-size: 20px; line-height: 23.6px;
    padding: 40px 10px 0 25px;
  }
  .photo-law {
    left: 40px; top: 312px; width: 195px; height: 175px;
    background: linear-gradient(120deg, #3c5c96 0%, #3f5f98 45%, #7a5238 70%, #b9a48c 100%);
  }
  .photo-hero {
    left: 39px; top: 501px; width: 744px; height: 343px;
    background: linear-gradient(180deg, #0e1d4a 0%, #1b3a6e 38%, #5a4a3a 60%, #a3704a 78%, #4a4d57 100%);
  }

  .meeting { position: absolute; }
  .meeting-join { background: var(--red); height: 77px; padding: 6px 0 0 22px; color: #fff; }
  .meeting-join .lead { font-family: "Arimo", sans-serif; font-weight: 700; font-size: 27px; line-height: 30px; letter-spacing: 0.3px; }
  .meeting-join .venue { font-family: "Anton", sans-serif; font-size: 27px; line-height: 34px; color: var(--dark-red); }
  .meeting-when { margin-top: 3px; background: var(--blue); height: 95px; display: flex; align-items: center; color: #fff; }
  .when-date { padding-left: 21px; width: 254px; border-right: 2px solid rgba(255,255,255,0.85); height: 78px; }
  .when-date .date { font-family: "Anton", sans-serif; font-size: 38px; line-height: 44px; }
  .when-date .date .hot, .when-date .time .hot { color: var(--red); }
  .when-date .time { font-family: "Arimo", sans-serif; font-weight: 700; font-size: 31px; line-height: 32px; }
  .when-place { display: flex; align-items: flex-start; padding-left: 16px; }
  .when-place svg { margin-top: 2px; margin-right: 14px; flex: none; }
  .when-place .place { font-family: "Arimo", sans-serif; font-weight: 700; font-size: 22px; line-height: 25px; }
  .when-place .place small { display: block; font-size: 18px; line-height: 21px; font-weight: 700; }

  .compensation {
    left: 30px; top: 862px; width: 763px; text-align: center;
    font-family: "Poppins", sans-serif; font-weight: 700; font-size: 28px; line-height: 35px; color: #2a2a2a;
  }
  .url-bar { left: 39px; top: 950px; width: 745px; height: 73px; background: var(--red); }

  .title-bar { left: 39px; top: 39px; width: 745px; height: 65px; background: #000; }

  .claims { left: 39px; top: 188px; width: 745px; display: grid; grid-template-columns: 387px 358px; }
  .claims ul { list-style: none; }
  .claims li {
    position: relative; padding-left: 29px; height: 51px;
    font-family: "Arimo", sans-serif; font-weight: 700; font-size: 16px; line-height: 18.5px; color: #1d1d1d;
  }
  .claims li::before { content: ""; position: absolute; left: 0; top: 6px; width: 9px; height: 9px; border-radius: 50%; background: var(--blue); }
  .claims .col-right li { padding-left: 26px; }

  .photo-site {
    left: 46px; top: 511px; width: 501px; height: 224px;
    background: linear-gradient(180deg, #7ea3cf 0%, #a9bfd8 35%, #4b6f93 62%, #2a5f8e 100%);
  }
  .demands { left: 547px; top: 511px; width: 234px; height: 224px; background: var(--red); padding: 26px 10px 0 27px; }
  .demands ul { list-style: none; }
  .demands li {
    position: relative; padding-left: 20px; margin-bottom: 16px;
    font-family: "Poppins", sans-serif; font-weight: 700; font-size: 13px; line-height: 16px; color: #fff;
  }
  .demands li::before { content: ""; position: absolute; left: 0; top: 4px; width: 8px; height: 8px; border-radius: 50%; background: #fff; }

  .badge-access { left: 46px; top: 752px; width: 102px; height: 76px; background: var(--blue); }
  .badge-stop { left: 177px; top: 752px; width: 76px; height: 76px; background: var(--red); }
  .rights-lettering {
    left: 42px; top: 838px; width: 212px; height: 96px;
    background: linear-gradient(90deg, #e7b3b4 0%, #e7b3b4 55%, #b9c0c9 100%);
  }
</style>
</head>
<body>
<div class="canvas">

  <section class="page page-one">
    <div class="abs teaser">What Was Once a Family Beachfront Is Now a Public Crisis Locals Say Seacliff Park Is Out of Control and No One’s Stopping It</div>

    <div class="abs photo-law" role="img" aria-label="Photo of a class action law book with a judge's gavel"></div>

    <div class="meeting" style="left:246px; top:312px; width:538px;">
      <div class="meeting-join">
        <div class="lead">JOIN US &amp; SHOW YOUR SUPPORT @</div>
        <div class="venue">PACIFIC SHORE TOWN COUNCIL MEETING</div>
      </div>
      <div class="meeting-when">
        <div class="when-date">
          <div class="date"><span class="hot">MAY 14,</span> 2025</div>
          <div class="time">TIME: <span class="hot">6:00 PM</span></div>
        </div>
        <div class="when-place">
          <svg width="28" height="28" viewBox="0 0 28 28" aria-hidden="true"><rect width="28" height="28" rx="5" fill="#d30f12"/><path d="M14 5a6 6 0 0 0-6 6c0 4.5 6 11 6 11s6-6.5 6-11a6 6 0 0 0-6-6z" fill="none" stroke="#fff" stroke-width="2.4"/><circle cx="14" cy="11" r="2" fill="#fff"/></svg>
          <div class="place">SEACLIFF PARK<br>COMMUNITY ROOM<small>(ABOVE THE ARCADE)</small></div>
        </div>
      </div>
    </div>

    <div class="abs photo-hero" role="img" aria-label="Night aerial photo of the seaside amusement park with wooden roller coaster and parking lot"></div>

    <div class="abs compensation">Multiple Lawsuits Filed Workers and Locals May Be Eligible for Compensation</div>
    <div class="abs url-bar"></div>

    <svg class="headline-art" viewBox="0 0 823 1058">
      <g class="display">
        <text x="39" y="95" font-size="52" fill="#111" textLength="439" lengthAdjust="spacingAndGlyphs">MAJOR PROBLEMS</text>
        <text x="39" y="203" font-size="112" fill="#d30f12" textLength="439" lengthAdjust="spacingAndGlyphs">EXPOSED</text>
        <text x="39" y="260" font-size="56" fill="#1466c6" textLength="439" lengthAdjust="spacingAndGlyphs">AT SEACLIFF PARK</text>
        <text x="41" y="304" font-size="40" fill="#111" textLength="685" lengthAdjust="spacingAndGlyphs">PACIFIC SHORE NEIGHBORS NEED YOUR HELP!</text>
        <text x="63" y="572" font-size="58" fill="#e0141a" textLength="620" lengthAdjust="spacingAndGlyphs">SEACLIFF PARK WAS BUILT</text>
        <text x="63" y="632" font-size="58" fill="#e0141a" textLength="652" lengthAdjust="spacingAndGlyphs">FOR FAMILIES — NOT RAVES</text>
        <text x="411" y="1010" font-size="66" fill="#fff" text-anchor="middle" textLength="648" lengthAdjust="spacingAndGlyphs">www.FixSeacliffPark.com</text>
      </g>
    </svg>
  </section>

  <section class="page page-two">
    <div class="abs title-bar"></div>

    <div class="abs claims">
      <ul class="col-left">
        <li>Accused of Running Drug and<br>Alcohol-Fueled Raves</li>
        <li>Illegal Raves Continue Despite City<br>Permit Denials</li>
        <li>Beloved Family Beachfront Turned into<br>Private Club</li>
        <li>100 Decibel Music Shatters Peace Half a<br>Mile Away</li>
        <li>Disabled Say Sonic Assaults Forced<br>Them Off the Beach</li>
        <li>Americans with Disability Act<br>Violations Appear Ignored</li>
      </ul>
      <ul class="col-right">
        <li>Toxic Waste Reportedly Dumped into<br>Public Storm Drains</li>
        <li>Millions in Public Revenue Possibly<br>Hidden from City</li>
        <li>Employees Report Wage Theft and<br>Dangerous Conditions</li>
        <li>Insiders Claim Paint Conceals<br>Dangerous Construction Defects</li>
        <li>Locals say Seacliff Park has Ruined<br>Pacific Shore</li>
        <li>Seacliff Mayhem Ties Up Police,<br>Firetrucks and Ambulances</li>
      </ul>
    </div>

    <div class="abs photo-site" role="img" aria-label="Photo of a row of blue portable toilets behind barricades beside the park's coaster and arcade building"></div>
    <div class="abs demands">
      <ul>
        <li>It’s Time To Take<br>A Stand</li>
        <li>We Need The Mayor<br>To Act Now.</li>
        <li>We Need Him To<br>Enforce The Lease.</li>
        <li>We Need YOU To<br>Show Up And Be Heard.</li>
      </ul>
    </div>

    <div class="abs badge-access" role="img" aria-label="Blue not-accessible sign"></div>
    <div class="abs badge-stop" role="img" aria-label="Stop sign reading no public access"></div>
    <div class="abs rights-lettering" role="img" aria-label="Lettering reading disability rights are civil rights"></div>

    <div class="meeting" style="left:278px; top:766px; width:502px;">
      <div class="meeting-join" style="height:72px; padding-top:4px; padding-left:20px;">
        <div class="lead" style="font-size:26px;">JOIN US &amp; SHOW YOUR SUPPORT @</div>
        <div class="venue" style="font-size:25px;">PACIFIC SHORE TOWN COUNCIL MEETING</div>
      </div>
      <div class="meeting-when" style="height:90px;">
        <div class="when-date" style="width:240px;">
          <div class="date"><span class="hot">MAY 14,</span> 2025</div>
          <div class="time">TIME: <span class="hot">6:00 PM</span></div>
        </div>
        <div class="when-place">
          <svg width="28" height="28" viewBox="0 0 28 28" aria-hidden="true"><rect width="28" height="28" rx="5" fill="#d30f12"/><path d="M14 5a6 6 0 0 0-6 6c0 4.5 6 11 6 11s6-6.5 6-11a6 6 0 0 0-6-6z" fill="none" stroke="#fff" stroke-width="2.4"/><circle cx="14" cy="11" r="2" fill="#fff"/></svg>
          <div class="place" style="font-size:21px; line-height:24px;">SEACLIFF PARK<br>COMMUNITY ROOM<small style="font-size:17px;">(ABOVE THE ARCADE)</small></div>
        </div>
      </div>
    </div>

    <div class="abs url-bar"></div>

    <svg class="headline-art" viewBox="0 0 823 1058">
      <g class="display">
        <text x="53" y="92" font-size="50" fill="#d30f12" textLength="707" lengthAdjust="spacingAndGlyphs">IS SEACLIFF PARK OUT OF CONTROL?</text>
        <text x="39" y="150" font-size="38" fill="#1466c6" textLength="745" lengthAdjust="spacingAndGlyphs">Explosive community claims demand answers:</text>
        <text x="411" y="1010" font-size="66" fill="#fff" text-anchor="middle" textLength="648" lengthAdjust="spacingAndGlyphs">www.FixSeacliffPark.com</text>
      </g>
    </svg>
  </section>

</div>
</body>
</html>
```